Business Card Design for Marketing Firm

Looking for business card design for higher end marketing firm. Clean but impressionable/trendy. We are a marketing firm that represents manufacturers in the foodservice equipment and supply industry. Our customers are end users such has hotels, restaurants, country clubs, convention centers and casinos as well as distributors of restaurants supplies and equipment, and manufacturers of foodservice equipment and supplies.
Target Market(s)
Hotels, Restaurants, Supply & Equipment Distributors, Foodservice Manufacturers
Industry/Entity Type
Foodservice/Hospitality
Contact Information for Business Card
Name, Title, Contact Number, Email, Website, Social Media, Address
Requirements
Must have
- Clean & Simple but Serious and Impressionable

```html
<!DOCTYPE html>
<html lang="en">
<head>
<meta charset="utf-8">
<title>Harbor Hospitality Reps – Business Card</title>
<link href="https://fonts.googleapis.com/css2?family=Open+Sans:wght@400;600;700&display=swap" rel="stylesheet">
<style>
  :root {
    --navy: #262a78;
    --ink: #2b2b2b;
    --paper: #ffffff;
    --backdrop: #2f2a27;
  }
  * { margin: 0; padding: 0; box-sizing: border-box; }
  html, body { width: 1200px; height: 786px; overflow: hidden; background: var(--backdrop); }
  .canvas { position: relative; width: 1200px; height: 786px; font-family: "Open Sans", Arial, sans-serif; }
  .card {
    position: absolute; top: 238px; width: 540px; height: 309px;
    background: var(--paper); overflow: hidden;
    box-shadow: 0 10px 28px rgba(0,0,0,0.45);
  }
  .card--contact { left: 40px; }
  .card--brand { left: 620px; }

  .edge-band { position: absolute; background: var(--navy); }
  .edge-band--left { left: 0; top: 0; bottom: 0; width: 16px; }
  .edge-band--bottom { left: 16px; right: 0; bottom: 0; height: 6px; }
  .edge-band--brand { left: 0; right: 0; bottom: 0; height: 8px; }

  .brand-name { color: var(--navy); font-weight: 600; text-align: center; line-height: 1.15; letter-spacing: 0.06em; }
  .card--contact .brand-name { position: absolute; left: 36px; top: 132px; width: 230px; font-size: 17px; }
  .card--brand .brand-name { position: absolute; left: 0; right: 0; top: 108px; font-size: 28px; }
  .brand-name__sub { display: block; font-size: 0.75em; letter-spacing: 0.2em; }

  .divider { position: absolute; left: 282px; top: 78px; width: 1.5px; height: 160px; background: var(--navy); }

  .contact { position: absolute; left: 300px; top: 76px; color: var(--ink); }
  .contact__name { color: var(--navy); font-weight: 700; font-size: 17px; letter-spacing: 0.02em; }
  .contact__title { font-size: 11px; margin-bottom: 10px; }
  .contact__line { display: flex; align-items: center; gap: 7px; font-size: 12px; margin-bottom: 4px; }
  .contact__icon { width: 12px; height: 12px; flex: none; }
  .contact__address { font-size: 12px; margin-top: 12px; padding-left: 19px; line-height: 1.45; }

  .social { position: absolute; left: 0; right: 0; top: 200px; display: flex; justify-content: center; gap: 6px; }
  .social__dot { width: 14px; height: 14px; border-radius: 50%; background: var(--navy); }
</style>
</head>
<body>
<div class="canvas">

  <section class="card card--contact">
    <div class="edge-band edge-band--left"></div>
    <div class="edge-band edge-band--bottom"></div>

    <div class="brand-name">HARBOR HOSPITALITY<span class="brand-name__sub">REPS</span></div>

    <div class="divider"></div>

    <div class="contact">
      <div class="contact__name">OWEN MARSH</div>
      <div class="contact__title">Managing Director</div>
      <div class="contact__line">
        <svg class="contact__icon" viewBox="0 0 12 12"><path fill="var(--navy)" d="M2.5 0.8 L4.4 2.9 L3.4 4.2 C4 5.6 6.2 7.9 7.8 8.6 L9.1 7.6 L11.2 9.5 L9.8 11.2 C5.5 11 1 6.5 0.8 2.2 Z"/></svg>
        <span>123 456 789</span>
      </div>
      <div class="contact__line">
        <svg class="contact__icon" viewBox="0 0 12 12"><rect x="0.8" y="2.5" width="10.4" height="7.5" fill="none" stroke="var(--navy)" stroke-width="1.4"/><path d="M1 3 L6 7 L11 3" fill="none" stroke="var(--navy)" stroke-width="1.4"/></svg>
        <span>info@yourmail.com</span>
      </div>
      <div class="contact__line">
        <svg class="contact__icon" viewBox="0 0 12 12"><circle cx="6" cy="6" r="5.2" fill="none" stroke="var(--navy)" stroke-width="1.3"/><ellipse cx="6" cy="6" rx="2.2" ry="5.2" fill="none" stroke="var(--navy)" stroke-width="1"/><path d="M1 6 H11" stroke="var(--navy)" stroke-width="1"/></svg>
        <span>www.yourwebsite.com</span>
      </div>
      <div class="contact__address">Your address, City<br>State, Zip 1234</div>
    </div>
  </section>

  <section class="card card--brand">
    <div class="brand-name">HARBOR HOSPITALITY<span class="brand-name__sub">REPS</span></div>
    <div class="social" aria-label="Social media links">
      <span class="social__dot"></span><span class="social__dot"></span><span class="social__dot"></span>
      <span class="social__dot"></span><span class="social__dot"></span><span class="social__dot"></span>
    </div>
    <div class="edge-band edge-band--brand"></div>
  </section>

</div>
</body>
</html>
```